Luxury Business Card Design for High-End Window Treatments

Gilded Slatworks
Custom Plantation Shutters & Architectural Shading Systems

⸻

BACK

Daniel Trevick
Owner

Custom Interior & Exterior Window Treatments

919-555-0148
gildedslatworks.com

I have included a picture that I’m hoping we can use on the back, but I’m also wondering if you can get rid of the ladder? Should we get rid of shutters , shades and blinds underneath Gilded Slatworks?

Target Market(s)

High-end residential homeowners, custom home builders, architects, interior designers, and luxury renovation clients seeking premium plantation shutters and motorized architectural shading systems.

Industry/Entity Type

Custom Window treatments

Contact Information for Business Card

Front Gilded Slatworks Custom Plantation Shutters Motorized Architectural Shading Systems BACK Daniel Trevick Owner 919-555-0148 GildedSlatworks.com Custom Interior & Exterior Window Treatments By Appointment

Requirements
Nice to have
• Not 100% sure on nice to halves or the color but you can definitely check out my website to get a better understanding of what I’m trying to do

```html
<!DOCTYPE html>
<html lang="en">
<head>
<meta charset="UTF-8">
<title>Gilded Slatworks — Business Card</title>
<link href="https://fonts.googleapis.com/css2?family=Lora:wght@400;600;700&family=Lato:wght@400&display=swap" rel="stylesheet">
<style>
  :root {
    --bg: #1c1b1c;
    --card: #0f0f0f;
    --card-edge: #1a1a1a;
    --silver: #e4e2dc;
    --ink: #f2f0ea;
    --gold: #f5c451;
    --gold-line: #b9912f;
    --band-text: #1a1406;
  }
  * { box-sizing: border-box; margin: 0; padding: 0; }
  html, body { width: 1200px; height: 939px; overflow: hidden; background: var(--bg); }
  .canvas {
    width: 1200px; height: 939px;
    display: flex; flex-direction: column; align-items: center; justify-content: center;
    gap: 39px;
  }
  .card {
    position: relative; width: 700px; height: 400px;
    border-radius: 22px; overflow: hidden;
    background: linear-gradient(135deg, var(--card-edge), var(--card) 60%);
    color: var(--ink);
  }

  /* Front */
  .front-logo {
    position: absolute; left: 0; right: 0; top: 105px; text-align: center;
    font-family: "Lora", serif; font-weight: 400; font-size: 54px; line-height: 1.05;
    color: var(--silver);
  }
  .front-services {
    position: absolute; left: 0; right: 0; top: 238px;
    display: flex; justify-content: center; gap: 22px;
    font-family: "Lora", serif; font-weight: 600; font-size: 22px; color: var(--gold);
  }
  .front-tagline {
    position: absolute; left: 0; right: 0; bottom: 44px; text-align: center;
    font-family: "Lora", serif; font-size: 15px; letter-spacing: 0.3px; color: var(--ink);
  }

  /* Back */
  .back-photo {
    position: absolute; left: 0; top: 0; width: 430px; height: 280px;
    background:
      linear-gradient(90deg, rgba(15,15,15,0) 55%, var(--card) 100%),
      linear-gradient(180deg, rgba(15,15,15,0) 55%, var(--card) 100%),
      linear-gradient(180deg, #8fb4d8 0%, #c9ccc8 32%, #4a4f55 55%, #3d4a35 80%, #2a3022 100%);
  }
  .back-logo {
    position: absolute; right: 40px; top: 44px; text-align: right;
    font-family: "Lora", serif; font-weight: 400; font-size: 40px; line-height: 1.05;
    color: var(--silver);
  }
  .rule {
    position: absolute; left: 70px; right: 40px; top: 252px; height: 1px;
    background: var(--gold-line);
  }
  .name {
    position: absolute; left: 70px; top: 206px;
    font-family: "Lora", serif; font-weight: 700; font-size: 30px; color: var(--ink);
  }
  .role {
    position: absolute; left: 72px; top: 260px;
    font-family: "Lato", sans-serif; font-size: 16px; color: var(--ink);
  }
  .contact {
    position: absolute; left: 72px; top: 298px; list-style: none;
    font-family: "Lato", sans-serif; font-size: 17px; color: var(--ink);
  }
  .contact li { display: flex; align-items: center; gap: 10px; height: 30px; }
  .contact svg { width: 14px; height: 14px; }
  .address {
    position: absolute; right: 40px; top: 264px; text-align: right;
    font-family: "Lato", sans-serif; font-size: 16px; line-height: 1.4; color: var(--ink);
  }
  .band { position: absolute; left: 0; top: 0; width: 700px; height: 400px; }
  .band-text {
    position: absolute; right: 40px; bottom: 16px;
    font-family: "Lora", serif; font-weight: 700; font-size: 16px; color: var(--band-text);
  }
</style>
</head>
<body>
<main class="canvas">
  <section class="card card--front">
    <div class="front-logo">Gilded<br>Slatworks</div>
    <div class="front-services"><span>Shutters</span><span>Shades</span><span>Blinds</span></div>
    <p class="front-tagline">Custom Plantation Shutters &amp; Motorized Architectural Shading Systems</p>
  </section>

  <section class="card card--back">
    <div class="back-photo" role="img" aria-label="Photo of a two-storey home with a screened porch fitted with exterior shades, trees and blue sky"></div>
    <div class="back-logo">Gilded<br>Slatworks</div>
    <svg class="band" viewBox="0 0 700 400" aria-hidden="true">
      <path d="M0 390 L250 390 C285 390 282 338 322 338 L700 338 L700 400 L0 400 Z" fill="var(--gold)"/>
    </svg>
    <h1 class="name">Daniel Trevick</h1>
    <div class="rule"></div>
    <p class="role">Owner</p>
    <ul class="contact">
      <li>
        <svg viewBox="0 0 24 24"><path fill="var(--ink)" d="M6.6 10.8a15.1 15.1 0 0 0 6.6 6.6l2.2-2.2a1 1 0 0 1 1-.25 11.4 11.4 0 0 0 3.6.57 1 1 0 0 1 1 1V20a1 1 0 0 1-1 1A17 17 0 0 1 3 4a1 1 0 0 1 1-1h3.5a1 1 0 0 1 1 1c0 1.25.2 2.45.57 3.57a1 1 0 0 1-.25 1z"/></svg>
        919-555-0148
      </li>
      <li>
        <svg viewBox="0 0 24 24"><circle cx="12" cy="12" r="10" fill="none" stroke="var(--ink)" stroke-width="2"/><ellipse cx="12" cy="12" rx="4" ry="10" fill="none" stroke="var(--ink)" stroke-width="2"/><line x1="2" y1="12" x2="22" y2="12" stroke="var(--ink)" stroke-width="2"/></svg>
        gildedslatworks.com
      </li>
    </ul>
    <p class="address">240 Orchard Ln, Suite 310 #2208<br>Brookhaven, NC 27999</p>
    <p class="band-text">Custom Interior &amp; Exterior Window Treatments</p>
  </section>
</main>
</body>
</html>
```